The Q Collective Business Cards

We need a sleek looking business card for our real estate company. Looking for a clean, modern, eye catching design on a standard size business card.
Updates

No more submissions please! Thank you!

Target Market(s)

General Public/Real Estate Clients

Industry/Entity Type

Real Estate

Contact Information for Business Card

Cards will be customized for each agent.

Colors

Designer to choose only greyscale colors for use in the design.

Requirements
Must have
• Black, white, gray color pallet, Photo area for headshot on the front of the card

```html
<!DOCTYPE html>
<html lang="en">
<head>
<meta charset="utf-8">
<title>The Q Collective – Business Cards</title>
<link href="https://fonts.googleapis.com/css2?family=Montserrat:wght@400;500;600&family=Roboto:wght@400&display=swap" rel="stylesheet">
<style>
  :root {
    --page-bg: #2b2b2b;
    --card-black: #1e1e1e;
    --card-front: #242424;
    --band-grey: #6d6d6d;
    --band-fold: #d9d9d9;
    --photo-light: #b9b3ac;
    --photo-dark: #6b5b4f;
    --white: #ffffff;
    --soft-white: #e6e6e6;
    --tag-band: #e9e9e9;
    --tag-text: #2a2a2a;
  }
  * { margin: 0; padding: 0; box-sizing: border-box; }
  html, body { width: 1200px; height: 1138px; overflow: hidden; }
  body { background: var(--page-bg); position: relative; font-family: "Roboto", Arial, sans-serif; }
  .card, .card * { white-space: nowrap; }

  .card { position: absolute; border-radius: 14px; overflow: hidden; }

  /* Logo side */
  .card--brand { left: 274px; top: 186px; width: 624px; height: 376px; background: var(--card-front); }
  .brand-mark { position: absolute; left: 0; right: 0; top: 150px; display: flex; align-items: center; justify-content: center; gap: 12px; }
  .brand-mark__square { width: 16px; height: 16px; background: var(--white); }
  .brand-mark__name { font-family: "Montserrat", Arial, sans-serif; font-weight: 500; font-size: 24px; letter-spacing: 5px; color: var(--white); }
  .brand-tagline { position: absolute; left: 226px; top: 268px; width: 172px; height: 22px; background: var(--tag-band); color: var(--tag-text); font-family: "Montserrat", Arial, sans-serif; font-weight: 500; font-size: 11px; letter-spacing: 2px; display: flex; align-items: center; justify-content: center; }
  .brokerage { position: absolute; left: 28px; top: 331px; display: flex; align-items: center; gap: 7px; font-size: 12px; color: var(--soft-white); letter-spacing: 0.3px; }
  .brokerage__dot { width: 10px; height: 10px; border-radius: 50%; background: var(--soft-white); }

  /* Agent side */
  .card--agent { left: 276px; top: 608px; width: 618px; height: 374px; background: var(--card-black); }
  .headshot { position: absolute; left: 0; top: 0; width: 295px; height: 374px; background: linear-gradient(160deg, var(--photo-light) 0%, #9c8f84 45%, var(--photo-dark) 100%); }
  .agent-brand { position: absolute; left: 321px; top: 37px; width: 257px; height: 53px; border: 1.5px solid var(--soft-white); display: flex; align-items: center; justify-content: center; gap: 9px; }
  .agent-brand__square { width: 11px; height: 11px; background: var(--white); }
  .agent-brand__name { font-family: "Montserrat", Arial, sans-serif; font-weight: 500; font-size: 17px; letter-spacing: 2px; color: var(--white); }
  .agent-tagline { position: absolute; left: 321px; top: 95px; width: 257px; text-align: center; font-family: "Montserrat", Arial, sans-serif; font-weight: 500; font-size: 11px; letter-spacing: 4px; color: var(--soft-white); }
  .name-band { position: absolute; left: 278px; top: 142px; width: 340px; height: 64px; background: var(--band-grey); padding: 7px 0 0 43px; }
  .name-fold { position: absolute; left: 278px; top: 206px; }
  .agent-name { font-family: "Montserrat", Arial, sans-serif; font-weight: 600; font-size: 23px; color: var(--white); line-height: 30px; }
  .agent-title { font-size: 16px; color: var(--soft-white); line-height: 20px; }
  .address { position: absolute; left: 321px; top: 215px; font-size: 17px; line-height: 24px; color: var(--white); }
  .contacts { position: absolute; left: 326px; top: 268px; list-style: none; }
  .contacts li { display: flex; align-items: center; height: 24px; font-size: 17px; color: var(--white); }
  .contacts svg { width: 14px; height: 14px; margin-right: 13px; fill: var(--soft-white); }
</style>
</head>
<body>

<section class="card card--brand">
  <div class="brand-mark">
    <span class="brand-mark__square"></span>
    <span class="brand-mark__name">THE Q COLLECTIVE</span>
  </div>
  <div class="brand-tagline">•REAL ESTATE TEAM•</div>
  <div class="brokerage"><span class="brokerage__dot"></span>RIVERBEND REALTY PARTNERS</div>
</section>

<section class="card card--agent">
  <div class="headshot" role="img" aria-label="Agent headshot photo"></div>

  <div class="agent-brand">
    <span class="agent-brand__square"></span>
    <span class="agent-brand__name">THE Q COLLECTIVE</span>
  </div>
  <div class="agent-tagline">•REAL ESTATE TEAM•</div>

  <div class="name-band">
    <div class="agent-name">Maya Delgado Price</div>
    <div class="agent-title">Real Estate Broker</div>
  </div>
  <svg class="name-fold" width="17" height="22" viewBox="0 0 17 22"><polygon points="0,0 17,0 17,22" fill="var(--band-fold)"/></svg>

  <div class="address">4120 Magnolia Ave<br>Cedar Falls, LA, US 70812</div>

  <ul class="contacts">
    <li><svg viewBox="0 0 16 16"><path d="M3 2h3l1.5 3.5-2 1.3a9 9 0 0 0 3.7 3.7l1.3-2L14 10v3a1 1 0 0 1-1 1A12 12 0 0 1 2 3a1 1 0 0 1 1-1z"/></svg>+1 555-014-2290</li>
    <li><svg viewBox="0 0 16 16"><path d="M1 3h14v10H1z M2 4v.4l6 4.3 6-4.3V4z" fill-rule="evenodd"/></svg>maya@qcollectivehomes.com</li>
    <li><svg viewBox="0 0 16 16"><path d="M8 1a7 7 0 1 0 0 14A7 7 0 0 0 8 1zm0 1.3c.8 0 1.7 1.5 2 3.7H6c.3-2.2 1.2-3.7 2-3.7zM2.4 7h2.5v2H2.4a5.7 5.7 0 0 1 0-2zm3.5 0h4.2v2H5.9zm5.2 0h2.5a5.7 5.7 0 0 1 0 2h-2.5zM6 10h4c-.3 2.2-1.2 3.7-2 3.7S6.3 12.2 6 10z"/></svg>www.qcollectivehomes.com</li>
  </ul>
</section>

</body>
</html>
```